Candle Rental Business seeks new website design

We need a new website design for a Candle hire business. The business rents out pillar candles for events such as weddings and corporate events. Our main target market is weddings. The business name is Hire a Lantern. The business name does not have a logo design.

We would like a website that is light in colours and creates a warm atmosphere. The design needs to be elegant and upmarket. There are different size candles that we hire out, ranging from 10cm diameter to 20cm diameter, flat, tall etc. All our candles are white in colour. Its just the size that differs.

We would also like to include a section for hiring out decor such as glassvases, candlebras, overlays and chairs sachets, chair covers. However, this is not the businesses main focus but an additional offering to customers.

Target Market(s)

Wedding venues and brides. Corporate events. School dances.

Industry/Entity Type

Hospitality

Logo Text

Hire a Lantern

Number of Pages Required

1 page

Font styles to use
Sans Serif
Script

Requirements
Must have
• Pictures of pillar candles. Plain white candles. The website must centre around candles.
Nice to have
• Different examples of candle centrepieces
Should not have
• Pictures must not be of brides. Pictures of surrounding is perferable.

```html
<!DOCTYPE html>
<html lang="en">
<head>
<meta charset="utf-8">
<title>Hire a Lantern</title>
<link href="https://fonts.googleapis.com/css2?family=Open+Sans:wght@300;400;600;700&display=swap" rel="stylesheet">
<style>
:root{
  --orange:#f39019;
  --orange-dark:#e07a0a;
  --ink:#3a3a3a;
  --muted:#777;
  --grey-bg:#efefef;
  --beige-bg:#f3efe4;
  --footer-bg:#e9e9e9;
  --white:#fff;
  --btn-grey:#5b5b5b;
}
*{box-sizing:border-box;margin:0;padding:0}
html,body{width:1200px;height:2756px;overflow:hidden}
body{font-family:"Open Sans",Arial,sans-serif;color:var(--ink);background:var(--white)}
.section-title{font-weight:300;font-size:46px;text-align:center;color:#333}

/* header */
.site-header{height:112px;position:relative;border-bottom:1px solid #ddd}
.brand{position:absolute;left:72px;top:30px;display:flex;align-items:center;gap:14px}
.brand-mark{width:44px;height:44px;border-radius:50%;background:var(--orange)}
.brand-name{font-size:34px;font-weight:600;color:var(--ink)}
.account-links{position:absolute;right:72px;top:12px;font-size:15px;color:var(--muted);display:flex;gap:30px}
.main-nav{position:absolute;right:72px;top:60px;display:flex;gap:18px;font-size:17px}
.main-nav a{color:var(--ink);text-decoration:none;padding:6px 14px}
.main-nav a.active{border:2px solid var(--orange);color:var(--orange)}

/* hero */
.hero{height:536px;position:relative;background:radial-gradient(ellipse at 45% 35%,#c79a63 0%,#6b5038 35%,#2a2420 75%,#1a1816 100%)}
.hero-caption{position:absolute;left:0;top:400px;width:760px;height:64px;background:linear-gradient(90deg,rgba(243,144,25,.85),rgba(243,144,25,.15));color:#fff;font-weight:700;font-size:27px;letter-spacing:.5px;line-height:64px;padding-left:60px}
.hero-arrow{position:absolute;top:240px;width:30px;height:56px}
.hero-arrow.prev{left:20px}.hero-arrow.next{right:20px}

/* about */
.about{height:292px;padding-top:48px;text-align:center}
.about p{width:1000px;margin:26px auto 0;font-size:15px;line-height:24px;color:var(--muted)}
.btn{display:inline-block;font-size:15px;color:#fff;padding:9px 22px;text-decoration:none}
.btn-orange{background:var(--orange)}
.btn-grey{background:var(--btn-grey)}
.about .btn{margin-top:28px}

/* products */
.products{height:620px;background:var(--grey-bg);padding-top:60px}
.product-grid{display:flex;gap:32px;justify-content:center;margin-top:50px}
.product-card{width:328px;height:432px;background:#fff}
.product-photo{height:200px}
.product-card h3{color:var(--orange);font-size:21px;font-weight:700;margin:16px 18px 8px}
.product-card p{font-size:14px;line-height:21px;color:var(--muted);margin:0 18px}
.product-actions{margin:48px 18px 0;display:flex;gap:14px}

/* how it works */
.how{height:460px;padding-top:60px;position:relative}
.steps{display:flex;justify-content:center;gap:128px;margin-top:66px}
.step{width:160px;text-align:center}
.step svg{display:block;margin:0 auto}
.step span{display:block;margin-top:22px;font-size:20px;line-height:26px;color:#444}

/* decor */
.decor{height:500px;background:var(--beige-bg);padding-top:60px}
.decor-grid{display:flex;gap:18px;justify-content:center;margin-top:56px}
.decor-tile{width:272px;height:200px;position:relative;display:flex;align-items:center;justify-content:center}
.decor-tile span{position:relative;color:#fff;font-size:24px;text-align:center;line-height:30px;text-shadow:0 1px 3px rgba(0,0,0,.6)}

/* footer */
.site-footer{height:200px;background:var(--footer-bg);padding:26px 72px 0;display:flex;gap:0}
.footer-col h4{font-size:16px;font-weight:600;margin-bottom:16px;color:#333}
.footer-col li{list-style:none;font-size:14px;color:#555;margin-bottom:10px;display:flex;align-items:center;gap:10px}
.col-links{width:230px}.col-contact{width:350px}.col-inquiry{width:400px}.col-follow{width:180px}
.bullet{width:6px;height:6px;background:#888;border-radius:50%}
.field{width:300px;height:26px;background:#fff;border:1px solid #ccc;margin-bottom:6px;font-size:12px;color:#999;padding:4px 8px}
.field.tall{height:44px}
.submit{width:300px;height:26px;background:var(--orange);color:#fff;font-size:14px;text-align:center;line-height:26px}
.social-dot{width:24px;height:24px;border-radius:50%}
.copyright{height:36px;background:var(--orange);color:#fff;font-size:14px;line-height:36px;padding:0 72px;display:flex;justify-content:space-between;align-items:center}
.pay-badges{display:flex;gap:6px;align-items:center}
.pay-badges i{display:block;width:34px;height:20px;background:#fff;border-radius:2px}
</style>
</head>
<body>

<header class="site-header">
  <div class="brand"><span class="brand-mark"></span><span class="brand-name">Hire a Lantern</span></div>
  <div class="account-links"><span>Log in</span><span>Register</span></div>
  <nav class="main-nav">
    <a class="active" href="#">Home</a><a href="#">About Us</a><a href="#">Our Products</a><a href="#">Contact Us</a>
  </nav>
</header>

<section class="hero" role="img" aria-label="Banquet tables lit by white pillar candles in glass vases">
  <svg class="hero-arrow prev" viewBox="0 0 30 56"><path d="M24 4 6 28l18 24" fill="none" stroke="#fff" stroke-width="4"/></svg>
  <svg class="hero-arrow next" viewBox="0 0 30 56"><path d="M6 4l18 24L6 52" fill="none" stroke="#fff" stroke-width="4"/></svg>
  <div class="hero-caption">WE DESIGN, MANUFACTURE &amp; PERSONALISE DECORATIVE CANDLES</div>
</section>

<section class="about">
  <h2 class="section-title">About Us</h2>
  <p>We are a family owned and operated candle hire business making decorative candles for all occasions. All of our candles are individually handmade in our candle studio, using only quality wax and tested wicks. Our range is made with care, giving a warm, even glow, and every piece is cleaned and checked before it goes out to your venue.</p>
  <a class="btn btn-orange" href="#">Read more</a>
</section>

<section class="products">
  <h2 class="section-title">Our Products</h2>
  <div class="product-grid">
    <article class="product-card">
      <div class="product-photo" role="img" aria-label="White pillar candles on a table centrepiece" style="background:linear-gradient(#cfd8c4,#9aa58a)"></div>
      <h3>Hire Candles</h3>
      <p>Do you love using candles for your events but tired of buying new ones each time? Hire ours and save on costly wax. Believe it or not, you can.</p>
      <div class="product-actions"><a class="btn btn-grey" href="#">Buy Now</a><a class="btn btn-orange" href="#">More Info</a></div>
    </article>
    <article class="product-card">
      <div class="product-photo" role="img" aria-label="Candles in stemmed glass holders" style="background:linear-gradient(#8d8278,#4e4640)"></div>
      <h3>Personalised Candles</h3>
      <p>Do you love using candles for your events but want them named? We print your words on each one so the night feels truly yours. Ask us today.</p>
      <div class="product-actions"><a class="btn btn-grey" href="#">Buy Now</a><a class="btn btn-orange" href="#">More Info</a></div>
    </article>
    <article class="product-card">
      <div class="product-photo" role="img" aria-label="Row of tall pillar candles of mixed sizes" style="background:linear-gradient(#c9c4ba,#8e887e)"></div>
      <h3>Décor Hire</h3>
      <p>Do you need more than candles for your event? Hire our vases, holders and chair covers to finish the room. Believe it or not, it costs less.</p>
      <div class="product-actions"><a class="btn btn-grey" href="#">Buy Now</a><a class="btn btn-orange" href="#">More Info</a></div>
    </article>
  </div>
</section>

<section class="how">
  <h2 class="section-title">How It Works</h2>
  <div class="steps">
    <div class="step">
      <svg width="160" height="160" viewBox="0 0 160 160"><circle cx="80" cy="80" r="78" fill="var(--orange-dark)"/><rect x="66" y="62" width="28" height="56" rx="3" fill="#fff"/><path d="M80 36c-8 10-8 16 0 22 8-6 8-12 0-22z" fill="#fff"/></svg>
      <span>Choose your Candle</span>
    </div>
    <div class="step">
      <svg width="160" height="160" viewBox="0 0 160 160"><circle cx="80" cy="80" r="78" fill="var(--orange)"/><path d="M72 44v50l-10-8-8 6 20 26h34l6-36-26-6V44z" fill="#fff"/></svg>
      <span>Book your Candle</span>
    </div>
    <div class="step">
      <svg width="160" height="160" viewBox="0 0 160 160"><circle cx="80" cy="80" r="78" fill="var(--orange-dark)"/><rect x="40" y="56" width="80" height="48" rx="4" fill="#fff"/><circle cx="80" cy="80" r="12" fill="var(--orange-dark)"/></svg>
      <span>Make payment</span>
    </div>
    <div class="step">
      <svg width="160" height="160" viewBox="0 0 160 160"><circle cx="80" cy="80" r="78" fill="#f8b21c"/><rect x="68" y="66" width="24" height="48" fill="#fff"/><rect x="56" y="112" width="48" height="8" fill="#fff"/><path d="M80 38c-7 9-7 15 0 22 7-7 7-13 0-22z" fill="#fff"/></svg>
      <span>Light Up Your Event</span>
    </div>
  </div>
</section>

<section class="decor">
  <h2 class="section-title">Our Hiring Out Decor</h2>
  <div class="decor-grid">
    <div class="decor-tile" role="img" aria-label="Glass vases with candles" style="background:linear-gradient(#5a5048,#2a2420)"><span>Glass Vases</span></div>
    <div class="decor-tile" role="img" aria-label="Candelabras on a dinner table" style="background:linear-gradient(#7a6a5a,#3a3028)"><span>Candle Bras</span></div>
    <div class="decor-tile" role="img" aria-label="Chairs dressed with overlays and sashes" style="background:linear-gradient(#6e6a66,#34302c)"><span>Overlays &amp;<br>Chairs Sachets</span></div>
    <div class="decor-tile" role="img" aria-label="White chair covers at a reception" style="background:linear-gradient(#d8ccd4,#a8949e)"><span>Chair Covers</span></div>
  </div>
</section>

<footer class="site-footer">
  <div class="footer-col col-links">
    <h4>Quick Links</h4>
    <ul><li><i class="bullet"></i>Home</li><li><i class="bullet"></i>About Us</li><li><i class="bullet"></i>Our Products</li><li><i class="bullet"></i>Contact Us</li></ul>
  </div>
  <div class="footer-col col-contact">
    <h4>Contact Details</h4>
    <ul>
      <li><svg width="14" height="18" viewBox="0 0 14 18"><path d="M7 0a7 7 0 0 0-7 7c0 5 7 11 7 11s7-6 7-11a7 7 0 0 0-7-7z" fill="#888"/></svg>48 Wick Lane, Emberton EM4 2LT</li>
      <li><svg width="14" height="16" viewBox="0 0 14 16"><path d="M3 0l3 4-2 2c1 2 3 4 5 5l2-2 3 3-2 3C6 15 0 8 0 2z" fill="#888"/></svg>(021) 555 0148</li>
      <li><svg width="16" height="12" viewBox="0 0 16 12"><rect width="16" height="12" fill="#888"/><path d="M0 0l8 6 8-6" fill="none" stroke="#fff"/></svg>hello@hirealantern.example</li>
    </ul>
  </div>
  <div class="footer-col col-inquiry">
    <h4>Quick Inquiry</h4>
    <div class="field">Name</div><div class="field">Phone</div><div class="field tall">Message</div><div class="submit">Submit</div>
  </div>
  <div class="footer-col col-follow">
    <h4>Follow Us</h4>
    <ul>
      <li><i class="social-dot" style="background:#3b5a98"></i>Friendwall</li>
      <li><i class="social-dot" style="background:#2fa8e0"></i>Chirper</li>
      <li><i class="social-dot" style="background:#1f77b0"></i>WorkLink</li>
      <li><i class="social-dot" style="background:#d34836"></i>SearchCircle</li>
    </ul>
  </div>
</footer>
<div class="copyright">
  <span>Copyright © 2016 Hire a Lantern. All Rights Reserved.</span>
  <div class="pay-badges"><span>We Accept</span><i></i><i></i><i></i></div>
</div>

</body>
</html>
```